Stationery Set for Velmora Company

I need to create full stationery design for my company; Business Cards, Envelops, Letter Heads, Calendar.
In the letter head and Envelops... only contact information and website links.
Our company is a Service Management company with different domains of innovative services including Technology Service Management, Education Services, Outsourcing Management, Events Management.
I need a modern and innovative design specially for the business card. I some transparent designs and I like it, but don't limit your innovation to what I mentioned. Sky is limit for your innovation.

Target Market(s)

Middle East & Africa

Industry/Entity Type

Business Management

Colors
34a7d8
0355a3
85acd3
86cae7
cee9f5
cfdeed
e4daeb
f3f1f8
ecf7fb

Requirements
Must have
• Name, Title, Email, Mobile
Nice to have
• We have multiple locations in USA, KSA, EGY, so I need ideas about how to include all contact details maybe QR / Barcode or something else.
• Please see our locations and contact information: www.brightvelmora.example
Should not have
• Too much text

```html
<!DOCTYPE html>
<html lang="en">
<head>
<meta charset="utf-8">
<title>Velmora Company – Business Card</title>
<link rel="stylesheet" href="https://fonts.googleapis.com/css2?family=Open+Sans:wght@400;600;700&display=swap">
<style>
  :root {
    --stage: #3d3d3d;
    --card-white: #ffffff;
    --brand-blue: #3e69b0;
    --stone: #c9c1bf;
    --ink: #2b2b2b;
    --white: #ffffff;
  }
  * { margin: 0; padding: 0; box-sizing: border-box; }
  html, body {
    width: 1105px; height: 1200px; overflow: hidden;
    background: var(--stage);
    font-family: "Open Sans", Arial, sans-serif;
  }
  .card {
    position: absolute; left: 196px; width: 720px; height: 411px; overflow: hidden;
  }
  .card--front { top: 146px; background: var(--card-white); }
  .card--back { top: 602px; background: var(--brand-blue); }

  .front-band { position: absolute; left: 0; top: 250px; width: 720px; height: 161px; }

  .wordmark {
    position: absolute; display: flex; align-items: center; gap: 10px;
    font-weight: 700; letter-spacing: 1px; line-height: 1;
  }
  .wordmark__dot { width: 18px; height: 18px; border-radius: 50%; background: var(--stone); }
  .card--front .wordmark { right: 44px; top: 56px; font-size: 46px; color: var(--brand-blue); }
  .card--back .wordmark { left: 0; right: 0; top: 130px; justify-content: center; font-size: 60px; color: var(--white); }
  .card--back .wordmark__dot { width: 22px; height: 22px; }

  .holder { position: absolute; left: 36px; top: 148px; }
  .holder__name { font-size: 29px; font-weight: 600; color: var(--brand-blue); line-height: 1.15; }
  .holder__title { font-size: 22px; color: var(--ink); line-height: 1.2; }

  .office { position: absolute; font-size: 19px; line-height: 26.5px; font-style: normal; }
  .office__country { font-weight: 700; }
  .office--saudi { left: 36px; top: 261px; color: var(--white); }
  .office--usa { right: 39px; top: 284px; text-align: right; color: var(--ink); }

  .contacts {
    position: absolute; left: 30px; right: 30px; top: 293px;
    color: var(--white); font-size: 17px; line-height: 28px; text-align: center;
  }
  .contacts__line { display: flex; justify-content: center; align-items: center; gap: 8px; white-space: nowrap; }
  .contacts__item { display: inline-flex; align-items: center; gap: 4px; }
  .icon { width: 16px; height: 16px; fill: var(--stone); flex: none; }
</style>
</head>
<body>

<section class="card card--front" aria-label="Business card front">
  <svg class="front-band" viewBox="0 0 720 161" aria-hidden="true">
    <rect width="720" height="161" fill="var(--brand-blue)"/>
    <path d="M312 161 L386 30 Q395 14 414 14 L720 14 L720 161 Z" fill="#ffffff"/>
    <path d="M318 161 L390 34 Q398 19 416 19 L720 19 L720 161 Z" fill="var(--stone)"/>
  </svg>

  <div class="wordmark"><span class="wordmark__dot"></span><span>VELMORA</span></div>

  <div class="holder">
    <p class="holder__name">Daniel Hart</p>
    <p class="holder__title">CEO/Founder</p>
  </div>

  <address class="office office--saudi">
    <span class="office__country">SAUDI</span><br>
    Riyadh, Al Nakheel,<br>
    Fahad Al Qamar St.<br>
    Noura Buildings<br>
    Block 4C 3rd Floor A12, A18
  </address>

  <address class="office office--usa">
    <span class="office__country">USA</span><br>
    418 Harbor Crest Drive<br>
    6th Floor Bayview City<br>
    CA 90210 US
  </address>
</section>

<section class="card card--back" aria-label="Business card back">
  <div class="wordmark"><span>VELMORA</span><span class="wordmark__dot"></span></div>

  <div class="contacts">
    <p class="contacts__line">
      <span class="contacts__item">
        <svg class="icon" viewBox="0 0 24 24" aria-hidden="true"><path d="M6.6 10.8a15.5 15.5 0 0 0 6.6 6.6l2.2-2.2a1 1 0 0 1 1-.25 11.4 11.4 0 0 0 3.6.57 1 1 0 0 1 1 1V20a1 1 0 0 1-1 1A17 17 0 0 1 3 4a1 1 0 0 1 1-1h3.5a1 1 0 0 1 1 1c0 1.25.2 2.45.57 3.57a1 1 0 0 1-.25 1z"/></svg>
        +1.5550104570 (USA)
      </span>
      <span class="contacts__item">
        <svg class="icon" viewBox="0 0 24 24" aria-hidden="true"><path d="M6.6 10.8a15.5 15.5 0 0 0 6.6 6.6l2.2-2.2a1 1 0 0 1 1-.25 11.4 11.4 0 0 0 3.6.57 1 1 0 0 1 1 1V20a1 1 0 0 1-1 1A17 17 0 0 1 3 4a1 1 0 0 1 1-1h3.5a1 1 0 0 1 1 1c0 1.25.2 2.45.57 3.57a1 1 0 0 1-.25 1z"/></svg>
        +966 90000 11 25 (Saudi)
      </span>
    </p>
    <p class="contacts__line">
      <span class="contacts__item">
        <svg class="icon" viewBox="0 0 24 24" aria-hidden="true"><path d="M7 1h10a2 2 0 0 1 2 2v18a2 2 0 0 1-2 2H7a2 2 0 0 1-2-2V3a2 2 0 0 1 2-2zm0 3v14h10V4zm5 15.2a1.2 1.2 0 1 0 0 2.4 1.2 1.2 0 0 0 0-2.4z"/></svg>
        +1.5550104570
      </span>
      <span class="contacts__item">
        <svg class="icon" viewBox="0 0 24 24" aria-hidden="true"><path d="M2 5h20v14H2zm2 2v.5l8 5 8-5V7zm0 2.8V17h16V9.8l-8 5z"/></svg>
        info@brightvelmora.example
      </span>
      <span class="contacts__item">
        <svg class="icon" viewBox="0 0 24 24" aria-hidden="true"><path d="M12 2a10 10 0 1 0 0 20 10 10 0 0 0 0-20zm6.9 6h-3a15 15 0 0 0-1.3-3.9A8 8 0 0 1 18.9 8zM12 4c.8 1.1 1.5 2.5 1.9 4h-3.8c.4-1.5 1.1-2.9 1.9-4zM4.3 14a8 8 0 0 1 0-4h3.4a16 16 0 0 0 0 4zm.8 2h3a15 15 0 0 0 1.3 3.9A8 8 0 0 1 5.1 16zm3-8h-3a8 8 0 0 1 4.3-3.9A15 15 0 0 0 8.1 8zM12 20c-.8-1.1-1.5-2.5-1.9-4h3.8c-.4 1.5-1.1 2.9-1.9 4zm2.3-6H9.7a14 14 0 0 1 0-4h4.6a14 14 0 0 1 0 4zm.3 5.9a15 15 0 0 0 1.3-3.9h3a8 8 0 0 1-4.3 3.9zm1.7-5.9a16 16 0 0 0 0-4h3.4a8 8 0 0 1 0 4z"/></svg>
        www.brightvelmora.example
      </span>
    </p>
  </div>
</section>

</body>
</html>
```